Marisa Tollworth writer

I need a design for my business cards I write verses quotes and put them on to canvas, for children adults.
I like the idea of a quill pen and I love colour and a bit of magic as words can be magical.
My email address is brenvale@postnook.example PH: 0400318742
Here is an example of what I write
Can you put this verse on it
WORDS
Words can bring a tear to the eye
Words can make a heart sigh
Words can colour a world thats bland
Words can help one understand

This one is just a sample of my type of writing to give you an idea of the feel i'm looking for.
You'r Freind
I promise to be there
When life seems unfair
Sit with you when you cry
Wiping that tear from your eye
Holding you through the pain
Until you smile again
On me you can depend
Always your friend
Marisa Tollworth (c)

Target Market(s)

My target market is everyone family friend lover .

Industry/Entity Type

Business

Colors

Designer to choose colors to be used in the design.

```html
<!DOCTYPE html>
<html lang="en">
<head>
<meta charset="utf-8">
<title>Marisa Tollworth – Business Card</title>
<link rel="stylesheet" href="https://fonts.googleapis.com/css2?family=Courgette&family=Noto+Serif:wght@400&display=swap">
<style>
  :root {
    --backdrop: #d9d6d0;
    --card-stock: #ecebe6;
    --ink-teal: #2e7c88;
    --ink-teal-deep: #266f7a;
    --edge-cyan: #6cd3e6;
    --card-shadow: rgba(40, 40, 40, 0.18);
  }
  * { box-sizing: border-box; margin: 0; padding: 0; }
  html, body {
    width: 1200px;
    height: 1000px;
    overflow: hidden;
    background: var(--backdrop);
  }
  .sheet {
    width: 1200px;
    height: 1000px;
    display: flex;
    flex-direction: column;
    align-items: center;
    justify-content: center;
    gap: 56px;
  }
  .card {
    position: relative;
    width: 740px;
    height: 420px;
    background: var(--card-stock);
    border-bottom: 8px solid var(--edge-cyan);
    box-shadow: 0 6px 22px var(--card-shadow);
    color: var(--ink-teal);
  }
  .brand {
    display: flex;
    align-items: center;
    white-space: nowrap;
  }
  .brand__dot {
    flex: none;
    border-radius: 50%;
    background: var(--ink-teal);
  }
  .brand__name {
    font-family: "Courgette", cursive;
    line-height: 1;
    color: var(--ink-teal);
  }

  /* Front face */
  .card--front {
    display: flex;
    flex-direction: column;
    justify-content: center;
    padding-left: 92px;
  }
  .card--front .brand { gap: 18px; }
  .card--front .brand__dot { width: 24px; height: 24px; }
  .card--front .brand__name { font-size: 66px; }
  .tagline {
    margin-top: 10px;
    margin-left: 48px;
    font-family: "Courgette", cursive;
    font-size: 20px;
    letter-spacing: 1px;
    color: var(--ink-teal-deep);
  }

  /* Back face */
  .card--back {
    padding: 60px 44px 40px 52px;
    display: flex;
    justify-content: space-between;
  }
  .identity {
    display: flex;
    flex-direction: column;
  }
  .identity .brand {
    gap: 10px;
    padding-bottom: 6px;
    border-bottom: 2px solid var(--ink-teal);
    box-shadow: 0 4px 0 -1px var(--card-stock), 0 5px 0 0 var(--ink-teal);
  }
  .identity .brand__dot { width: 16px; height: 16px; }
  .identity .brand__name { font-size: 42px; }
  .contact {
    margin-top: 40px;
    font-family: "Noto Serif", serif;
    font-size: 17px;
    line-height: 1.3;
  }
  .contact__name {
    font-family: "Courgette", cursive;
    font-size: 25px;
    margin-bottom: 12px;
  }
  .offer {
    width: 220px;
    text-align: center;
    padding-top: 26px;
  }
  .offer__script {
    font-family: "Courgette", cursive;
    font-size: 24px;
    line-height: 1.2;
  }
  .offer__caps {
    font-family: "Noto Serif", serif;
    font-size: 27px;
    line-height: 1.15;
  }
  .offer__you {
    font-family: "Courgette", cursive;
    font-size: 48px;
    line-height: 1.05;
  }
</style>
</head>
<body>
  <main class="sheet">
    <section class="card card--front" aria-label="Card front">
      <div class="brand">
        <span class="brand__dot"></span>
        <span class="brand__name">Marisa Tollworth</span>
      </div>
      <p class="tagline">writer · poet · artist</p>
    </section>

    <section class="card card--back" aria-label="Card back">
      <div class="identity">
        <div class="brand">
          <span class="brand__dot"></span>
          <span class="brand__name">Marisa Tollworth</span>
        </div>
        <div class="contact">
          <p class="contact__name">Marisa Tollworth</p>
          <p>brenvale@postnook.example</p>
          <p>0400318742</p>
          <p>marisatollworth.example</p>
        </div>
      </div>
      <div class="offer">
        <p class="offer__script">verses &amp; quotes</p>
        <p class="offer__caps">ON CANVAS</p>
        <p class="offer__script">specially made</p>
        <p class="offer__caps">FOR</p>
        <p class="offer__you">You</p>
      </div>
    </section>
  </main>
</body>
</html>
```